Lanterns of Brackenmoor Podcast

We need a Podcast Cover design that is compatible with Apple Podcasts, Spotify, etc. In this podcast, we interview the real movers & shakers in the foodservice industry who cut through the noise to get to the top.

```html
<!DOCTYPE html>
<html lang="en">
<head>
<meta charset="utf-8">
<title>Lanterns of Brackenmoor Podcast – Cover</title>
<link rel="stylesheet" href="https://fonts.googleapis.com/css2?family=Bebas+Neue&display=swap">
<style>
  :root {
    --paper: #ffffff;
    --sun: #fcb91e;
    --navy: #02152b;
    --frame: #3a4f9c;
  }
  html, body {
    margin: 0;
    padding: 0;
    width: 1200px;
    height: 1200px;
    overflow: hidden;
    background: var(--paper);
  }
  .cover {
    display: block;
    width: 1200px;
    height: 1200px;
  }
  .cover-panel {
    fill: var(--sun);
    stroke: var(--frame);
    stroke-width: 9;
  }
  .title-text {
    font-family: "Bebas Neue", "Oswald", sans-serif;
    fill: var(--navy);
  }
  .rule { stroke: var(--navy); stroke-width: 4; }
  .flourish { stroke: var(--navy); stroke-width: 2.5; fill: none; stroke-linecap: round; }
  .art-slot { fill: var(--navy); }
</style>
</head>
<body>
<svg class="cover" viewBox="0 0 1200 1200" xmlns="http://www.w3.org/2000/svg" aria-labelledby="cover-title">
  <title id="cover-title">Lanterns of Brackenmoor Podcast</title>
  <defs>
    <filter id="panel-shadow" x="-5%" y="-5%" width="110%" height="110%">
      <feDropShadow dx="2" dy="4" stdDeviation="4" flood-color="#000" flood-opacity="0.35"/>
    </filter>
  </defs>

  <rect class="cover-panel" x="146" y="146" width="918" height="918" filter="url(#panel-shadow)"/>

  <!-- top line: "Lanterns of" with spoon artwork -->
  <text class="title-text" x="240" y="340" font-size="108" textLength="396" lengthAdjust="spacingAndGlyphs">LANTERNS OF</text>
  <rect class="art-slot" x="664" y="258" width="309" height="82" rx="41" role="img" aria-label="Spoon silhouette illustration"/>

  <!-- upper divider with bow tie -->
  <line class="rule" x1="240" y1="363" x2="574" y2="363"/>
  <rect class="art-slot" x="580" y="352" width="50" height="24" rx="6" role="img" aria-label="Bow tie ornament"/>
  <line class="rule" x1="636" y1="363" x2="972" y2="363"/>

  <!-- main name -->
  <text class="title-text" x="244" y="703" font-size="400" textLength="729" lengthAdjust="spacingAndGlyphs">BRACKENMOOR</text>

  <!-- lower divider with bow tie -->
  <line class="rule" x1="240" y1="723" x2="574" y2="723"/>
  <rect class="art-slot" x="580" y="711" width="50" height="24" rx="6" role="img" aria-label="Bow tie ornament"/>
  <line class="rule" x1="636" y1="723" x2="972" y2="723"/>

  <!-- bottom line: fork artwork with "Podcast" -->
  <rect class="art-slot" x="236" y="758" width="302" height="50" rx="25" role="img" aria-label="Fork silhouette illustration"/>
  <text class="title-text" x="567" y="806" font-size="74" textLength="406" lengthAdjust="spacing">PODCAST</text>

  <!-- flourish rules -->
  <path class="flourish" d="M437 958 H250 C238 958 234 950 238 946 C242 942 248 946 246 950"/>
  <path class="flourish" d="M769 958 H957 C969 958 973 950 969 946 C965 942 959 946 961 950"/>
</svg>
</body>
</html>
```